I am looking to create a newly designed website for our national leadership conference which is entitled, "The Harbor of Momentum Leadership Summit". The Harbor of Momentum Leadership Summit is a national conference for student leaders that prepares them for career leadership success. The current website can be seen at www.harborofmomentumleadershipsummit.com.

My goal for the new site is to create a more updated, fresh, hip, and exciting look that appeals to the younger generation while also maintaining are professional appeal. The color should be black, white, and gold. We want there to be live videos played and places to insert pictures for the panels as well.

I look forward to seeing you the new creations.

Requirements
Must have
• Ability to play videos on the home page and throughout the website. Also, make sure that the website shows up clearly on an zTablet.
Nice to have
• Nice look

```html
<!DOCTYPE html>
<html lang="en">
<head>
<meta charset="utf-8">
<title>Harbor of Momentum Leadership Summit</title>
<link rel="stylesheet" href="https://fonts.googleapis.com/css2?family=Montserrat:wght@400;500;600&family=Open+Sans:wght@400;600&display=swap">
<style>
  :root {
    --cream: #eeeae3;
    --ink: #000000;
    --text-dark: #2b2b2b;
    --text-light: #e8e8e8;
    --muted: #6b6b6b;
    --gold-light: #dcb96e;
    --gold-dark: #b88c3e;
    --count-gold: #f4c644;
    --frame: #2f2f2f;
  }
  * { box-sizing: border-box; margin: 0; padding: 0; }
  html, body { width: 978px; height: 1200px; overflow: hidden; background: var(--ink); }
  body { position: relative; font-family: "Open Sans", sans-serif; color: var(--text-light); }
  .abs { position: absolute; }
  .heading { font-family: "Montserrat", sans-serif; font-weight: 500; text-transform: uppercase; }

  /* Header */
  .site-header { left: 0; top: 0; width: 978px; height: 104px; background: var(--cream); }
  .brand { left: 90px; top: 20px; display: flex; flex-direction: column; align-items: flex-start; gap: 12px; }
  .brand-mark { width: 44px; height: 44px; border-radius: 50%; background: linear-gradient(180deg, var(--gold-light), var(--gold-dark)); margin-left: 50px; }
  .brand-name { font-family: "Montserrat", sans-serif; font-weight: 600; font-size: 12.5px; letter-spacing: 1px; color: #3a3a3a; text-transform: uppercase; }
  .follow { right: 91px; top: 27px; display: flex; align-items: center; gap: 5px; font-size: 8.5px; color: var(--muted); }
  .follow span { margin-right: 3px; }
  .social { width: 16px; height: 16px; background: #4a78b5; }
  .social.alt { background: #b23a2f; }
  .main-nav { left: 306px; top: 66px; display: flex; height: 37px; }
  .main-nav a { font-family: "Montserrat", sans-serif; font-size: 9.6px; font-weight: 500; color: var(--text-dark); text-decoration: none; line-height: 37px; padding: 0 12.5px; }
  .main-nav a.active { background: linear-gradient(180deg, var(--gold-light), var(--gold-dark)); padding: 0 13px; margin-right: 0; }

  /* Hero */
  .hero { left: 90px; top: 124px; width: 797px; height: 354px; border: 3px solid var(--frame); background: linear-gradient(160deg, #24335f 0%, #6a4b5a 40%, #b36a4c 60%, #3a3f66 100%); }
  .hero-arrow { top: 158px; width: 24px; height: 24px; }
  .hero-caption { left: 0; bottom: 0; width: 100%; height: 72px; background: rgba(60,60,60,.72); }
  .hero-title { left: 27px; top: 27px; font-size: 19px; color: #fff; }
  .countdown { right: 17px; top: 10px; display: flex; gap: 12px; }
  .count-box { width: 58px; height: 52px; background: var(--count-gold); color: #2b2b2b; text-align: center; }
  .count-box b { display: block; font-family: "Montserrat", sans-serif; font-size: 21px; font-weight: 500; line-height: 30px; padding-top: 2px; }
  .count-box small { font-size: 9px; text-transform: uppercase; }

  /* Welcome */
  .welcome-title { left: 90px; top: 507px; font-size: 17.5px; color: #fff; }
  .welcome-text { left: 90px; top: 538px; width: 600px; font-size: 9.6px; line-height: 21px; color: var(--text-light); }
  .register-btn { left: 714px; top: 524px; width: 172px; height: 47px; background: linear-gradient(180deg, var(--gold-light), var(--gold-dark)); font-family: "Montserrat", sans-serif; font-size: 12.5px; font-weight: 500; color: #1e1e1e; display: flex; align-items: center; justify-content: center; gap: 5px; border-radius: 2px; }
  .divider { left: 90px; top: 594px; width: 797px; height: 4px; background: repeating-linear-gradient(135deg, #3a3a3a 0 1px, transparent 1px 3px); }
  .section-title { left: 90px; top: 621px; font-size: 17.5px; color: #fff; }
  .video { top: 665px; width: 388px; height: 201px; border: 3px solid var(--frame); display: flex; align-items: center; justify-content: center; }
  .video.one { left: 90px; background: linear-gradient(135deg, #3a4a6a 0%, #8a8a9a 45%, #2a3a5a 100%); }
  .video.two { left: 500px; width: 387px; background: linear-gradient(180deg, #e7dcc6 0%, #c49a5c 55%, #7a4e2a 100%); }

  /* Partners */
  .partners { left: 0; top: 894px; width: 978px; height: 122px; background: var(--cream); }
  .partner-title { top: 24px; font-size: 12.5px; color: #222; }
  .pager { top: 25px; display: flex; gap: 8px; }
  .partner-row { top: 56px; display: flex; align-items: center; }
  .badge { background: #c9c2b6; }
  .partner-divider { left: 487px; top: 20px; width: 1px; height: 82px; background: #b5aea2; }

  /* Footer */
  .footer-title { top: 1038px; font-size: 13.5px; color: #fff; }
  .footer-note { left: 90px; top: 1063px; font-size: 8.5px; }
  .email-field { left: 90px; top: 1087px; width: 160px; height: 31px; background: #fff; border-radius: 2px; font-size: 8px; color: #999; padding: 10px 9px; }
  .go-btn { left: 258px; top: 1088px; width: 52px; height: 29px; background: linear-gradient(180deg, var(--gold-light), var(--gold-dark)); border-radius: 2px; font-family: "Montserrat", sans-serif; font-size: 8.5px; font-weight: 600; color: #fff; text-align: center; line-height: 29px; }
  .footer-links { top: 1063px; list-style: none; }
  .footer-links li { font-size: 8.8px; line-height: 21px; color: var(--text-light); }
  .copyright { left: 0; top: 1167px; width: 978px; text-align: center; font-size: 8.5px; color: #6a6a6a; }
</style>
</head>
<body>

<header class="site-header abs">
  <div class="brand abs">
    <div class="brand-mark"></div>
    <div class="brand-name">Harbor of Momentum</div>
  </div>
  <div class="follow abs">
    <span>FOLLOW ON :</span>
    <i class="social"></i><i class="social"></i><i class="social"></i><i class="social"></i><i class="social alt"></i>
  </div>
  <nav class="main-nav abs">
    <a class="active">HOME</a><a>ABOUT</a><a>CONFERENCE</a><a>REGISTER</a><a>TESTIMONIALS</a><a>Y FACTOR</a><a>VIDEOS</a><a>CONTACT</a>
  </nav>
</header>

<section class="hero abs" role="img" aria-label="Speaker at a podium facing a large conference audience">
  <svg class="hero-arrow abs" style="left:13px" viewBox="0 0 24 24"><circle cx="12" cy="12" r="10" fill="none" stroke="#bbb" stroke-width="2"/><path d="M14 7l-5 5 5 5" fill="none" stroke="#bbb" stroke-width="2"/></svg>
  <svg class="hero-arrow abs" style="right:13px" viewBox="0 0 24 24"><circle cx="12" cy="12" r="10" fill="none" stroke="#bbb" stroke-width="2"/><path d="M10 7l5 5-5 5" fill="none" stroke="#bbb" stroke-width="2"/></svg>
  <div class="hero-caption abs">
    <h1 class="hero-title heading abs">6th Annual Conference Countdown</h1>
    <div class="countdown abs">
      <div class="count-box"><b>0</b><small>Hour</small></div>
      <div class="count-box"><b>0</b><small>Minutes</small></div>
      <div class="count-box"><b>0</b><small>Seconds</small></div>
    </div>
  </div>
</section>

<h2 class="welcome-title heading abs">Welcome to Harbor of Momentum Leadership Summit</h2>
<p class="welcome-text abs">for a transformational leadership experience that will connect you with an incredible diverse leadership network of students and professionals that provide you with the inspiration and leadership/professional skills needed to take your life to the next level!</p>
<div class="register-btn abs">
  <svg width="11" height="11" viewBox="0 0 12 12"><circle cx="6" cy="3.5" r="3" fill="#1e1e1e"/><path d="M0 12c0-4 2.5-5.5 6-5.5S12 8 12 12z" fill="#1e1e1e"/></svg>
  REGISTER NOW !
</div>
<div class="divider abs"></div>

<h2 class="section-title heading abs">Latest Conference</h2>
<div class="video one abs" role="img" aria-label="Audience applauding at the conference, video thumbnail">
  <svg width="42" height="42" viewBox="0 0 42 42"><circle cx="21" cy="21" r="19" fill="rgba(0,0,0,.15)" stroke="#eee" stroke-width="3"/><path d="M16 12l13 9-13 9z" fill="#eee"/></svg>
</div>
<div class="video two abs" role="img" aria-label="Lecture hall filled with attendees facing a stage, video thumbnail">
  <svg width="42" height="42" viewBox="0 0 42 42"><circle cx="21" cy="21" r="19" fill="rgba(0,0,0,.15)" stroke="#eee" stroke-width="3"/><path d="M16 12l13 9-13 9z" fill="#eee"/></svg>
</div>

<section class="partners abs">
  <h3 class="partner-title heading abs" style="left:90px">Network with Executives</h3>
  <svg class="pager abs" style="left:450px" width="30" height="12" viewBox="0 0 30 12"><path d="M7 1L2 6l5 5M21 1l5 5-5 5" fill="none" stroke="#333" stroke-width="2"/></svg>
  <div class="partner-row abs" style="left:95px;gap:22px">
    <div class="badge" style="width:76px;height:30px"></div>
    <div class="badge" style="width:50px;height:30px"></div>
    <div class="badge" style="width:82px;height:33px;background:#222"></div>
    <div class="badge" style="width:74px;height:22px"></div>
  </div>
  <div class="partner-divider abs"></div>
  <h3 class="partner-title heading abs" style="left:498px">Connect with other Student Leaders from</h3>
  <svg class="pager abs" style="left:858px" width="30" height="12" viewBox="0 0 30 12"><path d="M7 1L2 6l5 5M21 1l5 5-5 5" fill="none" stroke="#333" stroke-width="2"/></svg>
  <div class="partner-row abs" style="left:506px;gap:26px">
    <div class="badge" style="width:50px;height:50px;border-radius:50%"></div>
    <div class="badge" style="width:50px;height:50px;border-radius:50%"></div>
    <div class="badge" style="width:50px;height:50px"></div>
    <div class="badge" style="width:50px;height:30px"></div>
    <div class="badge" style="width:58px;height:34px"></div>
  </div>
</section>

<footer>
  <h4 class="footer-title heading abs" style="left:90px">Newsletter</h4>
  <p class="footer-note abs">Enter Email to join our mailing list</p>
  <div class="email-field abs">Email Address</div>
  <div class="go-btn abs">GO</div>

  <h4 class="footer-title heading abs" style="left:386px">Quick Links</h4>
  <ul class="footer-links abs" style="left:386px"><li>Conference</li><li>Videos</li><li>Testimonials</li></ul>
  <h4 class="footer-title heading abs" style="left:533px">About Us</h4>
  <ul class="footer-links abs" style="left:533px"><li>Who We Are?</li><li>Our Services</li><li>Why Choose Us?</li></ul>
  <h4 class="footer-title heading abs" style="left:678px">Company</h4>
  <ul class="footer-links abs" style="left:678px"><li>Privacy Policy</li><li>Terms and Conditions</li><li>Sitemap</li></ul>
  <h4 class="footer-title heading abs" style="left:830px">Help</h4>
  <ul class="footer-links abs" style="left:830px"><li>Call Us</li><li>Send Mail</li><li>FAQ</li></ul>

  <p class="copyright abs">Copyright@ 2015 The Harbor of Momentum Leadership Summit. All Right Reserved.</p>
</footer>

</body>
</html>
```